Small Business Broker Business Card Design

A business card design for a small business brokerage, which is a financial service, not unlike real estate brokerage, but for small businesses such as laundromats, pizza shops, restaurants, cleaners etc. The designs should all be simple, more conservative in nature, using the colors and font of the logo. Again, think real estate Brokerage as a business context
Contact Information for Business Card
Name: Glen R. Harlow. Title: Small Business Advisor. Email: g.harlow@bayfieldcapitalworks.example. Mobile: (555) 274-3918. Office: (555) 806-2147. www.bayfieldcapitalworks.example

```html
<!DOCTYPE html>
<html lang="en">
<head>
<meta charset="utf-8">
<title>Bayfield Capital Works – Business Card</title>
<link rel="stylesheet" href="https://fonts.googleapis.com/css2?family=Montserrat:wght@600;700&family=Arimo:wght@400&display=swap">
<style>
  :root {
    --backdrop: #2e2a28;
    --navy: #173a6b;
    --navy-light: #2c4f80;
    --green: #8cc63f;
    --white: #ffffff;
  }
  * { margin: 0; padding: 0; box-sizing: border-box; }
  html, body { width: 1200px; height: 716px; overflow: hidden; }
  body {
    background: var(--backdrop);
    position: relative;
    font-family: "Arimo", Arial, sans-serif;
  }
  .card {
    position: absolute;
    top: 203px;
    width: 540px;
    height: 309px;
    background: var(--navy);
    color: var(--white);
    box-shadow: 0 10px 30px rgba(0,0,0,.45);
  }
  .card-front { left: 40px; border-bottom: 4px solid var(--green); }
  .card-back {
    left: 620px;
    background: radial-gradient(circle at 20% 20%, var(--navy-light), var(--navy) 65%);
  }

  .brand { display: flex; flex-direction: column; align-items: center; }
  .brand-row { display: flex; align-items: center; gap: 10px; }
  .brand-mark { width: 16px; height: 16px; background: var(--green); }
  .brand-name {
    font-family: "Montserrat", sans-serif;
    font-weight: 700;
    text-transform: uppercase;
    letter-spacing: .06em;
    color: var(--white);
    white-space: nowrap;
  }
  .brand-tagline {
    font-family: "Montserrat", sans-serif;
    font-weight: 600;
    text-transform: uppercase;
    letter-spacing: .12em;
    color: var(--green);
    margin-top: 6px;
    white-space: nowrap;
  }

  .card-front .brand {
    position: absolute; inset: 0; justify-content: center;
  }
  .card-front .brand-name { font-size: 21px; }
  .card-front .brand-tagline { font-size: 9.5px; }

  .card-back .brand {
    position: absolute; top: 78px; left: 170px; width: 340px;
  }
  .card-back .brand-mark { width: 12px; height: 12px; }
  .card-back .brand-name { font-size: 15px; }
  .card-back .brand-tagline { font-size: 7px; margin-top: 5px; }

  .advisor {
    position: absolute; top: 176px; left: 16px; width: 210px; text-align: right;
  }
  .advisor-name {
    font-family: "Montserrat", sans-serif;
    font-weight: 600;
    font-size: 18px;
    text-transform: uppercase;
    color: var(--green);
    letter-spacing: .02em;
    white-space: nowrap;
  }
  .advisor-title { font-size: 13px; margin-top: 4px; white-space: nowrap; }

  .divider {
    position: absolute; top: 160px; left: 240px;
    width: 1px; height: 100px; background: var(--green);
  }

  .contact-list {
    position: absolute; top: 166px; left: 258px; list-style: none;
  }
  .contact-item {
    display: flex; align-items: center; gap: 9px;
    font-size: 13px; line-height: 22px; white-space: nowrap;
  }
  .contact-icon { width: 12px; height: 12px; flex: none; }
</style>
</head>
<body>
  <section class="card card-front" aria-label="Card front">
    <div class="brand">
      <div class="brand-row">
        <span class="brand-mark"></span>
        <span class="brand-name">Bayfield Capital Works, Inc</span>
      </div>
      <p class="brand-tagline">Buy or sell your neighborhood business with ease</p>
    </div>
  </section>

  <section class="card card-back" aria-label="Card back">
    <div class="brand">
      <div class="brand-row">
        <span class="brand-mark"></span>
        <span class="brand-name">Bayfield Capital Works, Inc</span>
      </div>
      <p class="brand-tagline">Buy or sell your neighborhood business with ease</p>
    </div>

    <div class="advisor">
      <h1 class="advisor-name">Glen R. Harlow</h1>
      <p class="advisor-title">Small Business Advisor</p>
    </div>

    <div class="divider"></div>

    <ul class="contact-list">
      <li class="contact-item">
        <svg class="contact-icon" viewBox="0 0 12 12" aria-hidden="true"><path d="M1 5c0-2 2-3 5-3s5 1 5 3l-2 1-1-1.5H4L3 6z M2.5 7h7v3.5h-7z" fill="#8cc63f"/></svg>
        (555) 806-2147
      </li>
      <li class="contact-item">
        <svg class="contact-icon" viewBox="0 0 12 12" aria-hidden="true"><rect x="3" y="0.5" width="6" height="11" rx="1" fill="none" stroke="#8cc63f" stroke-width="1.2"/><circle cx="6" cy="9.5" r=".7" fill="#8cc63f"/></svg>
        (555) 274-3918
      </li>
      <li class="contact-item">
        <svg class="contact-icon" viewBox="0 0 12 12" aria-hidden="true"><rect x="0.5" y="2.5" width="11" height="7.5" fill="#8cc63f"/><path d="M0.5 2.5l5.5 4.5 5.5-4.5" fill="none" stroke="#173a6b" stroke-width="1"/></svg>
        g.harlow@bayfieldcapitalworks.example
      </li>
      <li class="contact-item">
        <svg class="contact-icon" viewBox="0 0 12 12" aria-hidden="true"><circle cx="6" cy="6" r="5.3" fill="none" stroke="#8cc63f" stroke-width="1.2"/><path d="M0.7 6h10.6M6 .7c-3 3-3 7.6 0 10.6M6 .7c3 3 3 7.6 0 10.6" fill="none" stroke="#8cc63f" stroke-width=".9"/></svg>
        www.bayfieldcapitalworks.example
      </li>
    </ul>
  </section>
</body>
</html>
```